Business Card Design

This is a new cafe in Wavell Heights.
My mantra / (updated) slogan is 'Nourishing Food. Coffee as its Best'
95% of food is produced from my own kitchen.
Breakfast and lunch items on the menu include lots of good stuff on sourdough, all natural smoothies, gluten/dairy free foods/treats as well as more traditional fare. Focus is on wholesome healthy food and fantastic coffee.
Colours are predominantly green from attached logo and black but happy for some coffee bean brown for effect.
Preferred font would be Dilennial UPC per attached logo / flyer.
We have a Friendbook page and Instagram account.

Industry/Entity Type

Business

Contact Information for Business Card

Meredith Tallis
Lumen Cafe
384 Pelling Street
Marlow Heights QLD 4178

```html
<!DOCTYPE html>
<html lang="en">
<head>
<meta charset="utf-8">
<title>Lumen Cafe – Business Card</title>
<link rel="stylesheet" href="https://fonts.googleapis.com/css2?family=Arvo:wght@400;700&family=Roboto:wght@500&display=swap">
<style>
  :root {
    --bean-brown: #4c3a2d;
    --leaf-green: #1b9a48;
    --paper: #ffffff;
    --ground: #efe7da;
    --ink-light: #fbf7f1;
    --frame-line: #c9c9c9;
  }
  * { box-sizing: border-box; margin: 0; padding: 0; }
  html, body { width: 1189px; height: 1200px; overflow: hidden; }
  body {
    background: var(--ground);
    font-family: "Arvo", serif;
    position: relative;
  }
  .card {
    position: absolute;
    left: 171px;
    width: 856px;
    height: 489px;
    box-shadow: 6px 8px 10px rgba(0,0,0,0.35);
    overflow: hidden;
  }
  .card--front { top: 66px; background: var(--paper); }
  .card--back { top: 626px; background: var(--bean-brown); color: var(--ink-light); text-align: center; }

  /* front: header */
  .header { position: absolute; left: 0; top: 0; width: 100%; height: 149px; }
  .brand {
    position: absolute; left: 42px; top: 46px;
    display: flex; align-items: center; gap: 14px;
    font-family: "Arvo", serif; font-weight: 700; font-size: 60px;
    color: var(--leaf-green); line-height: 1;
  }
  .brand-dot { width: 22px; height: 22px; border-radius: 50%; background: var(--leaf-green); }
  .contact { position: absolute; right: 35px; top: 50px; text-align: right; line-height: 1.15; }
  .contact-name { font-family: "Arvo", serif; font-weight: 700; font-size: 28px; color: var(--leaf-green); }
  .contact-phone { font-family: "Roboto", sans-serif; font-weight: 500; font-size: 27px; color: var(--bean-brown); }

  .tagline-band {
    position: absolute; left: 0; top: 149px; width: 100%; height: 36px;
    background: var(--bean-brown); color: var(--ink-light);
    font-size: 22px; line-height: 36px; text-align: center;
  }

  .gallery { position: absolute; left: 0; top: 185px; width: 100%; height: 239px; }
  .photo-frame {
    position: absolute; top: 13px; width: 198px; height: 213px;
    border: 1px solid var(--frame-line); background: var(--paper); padding: 12px;
  }
  .photo-frame:nth-child(1) { left: 10px; }
  .photo-frame:nth-child(2) { left: 223px; }
  .photo-frame:nth-child(3) { left: 435px; }
  .photo-frame:nth-child(4) { left: 648px; }
  .photo { width: 100%; height: 100%; }
  .photo--latte { background: radial-gradient(circle at 50% 35%, #d9b88e 0 25%, #5a2e22 45%, #7f9a3a 70%, #222 100%); }
  .photo--cupcakes { background: radial-gradient(circle at 50% 55%, #f3d0d8 0 30%, #5a3526 55%, #121212 100%); }
  .photo--avocado-toast { background: linear-gradient(160deg, #8fbf3a 0%, #eeeae0 35%, #9fb547 65%, #c87040 100%); }
  .photo--tomato-toast { background: linear-gradient(160deg, #f1f0ea 0%, #cf4b2a 40%, #7c5a3e 75%, #c96a3b 100%); }

  .address-band {
    position: absolute; left: 0; bottom: 0; width: 100%; height: 65px;
    background: var(--bean-brown); color: var(--ink-light);
    font-size: 23px; line-height: 65px; text-align: center;
  }

  /* back */
  .headline { position: absolute; top: 148px; width: 100%; font-size: 29px; font-weight: 400; letter-spacing: 0.3px; }
  .menu { position: absolute; top: 212px; width: 100%; font-size: 25px; line-height: 33px; }
  .social { position: absolute; top: 398px; width: 100%; font-size: 24px; }
</style>
</head>
<body>
  <section class="card card--front">
    <header class="header">
      <div class="brand"><span class="brand-dot"></span>Lumen Cafe</div>
      <div class="contact">
        <div class="contact-name">Meredith Tallis</div>
        <div class="contact-phone">0412 555 097</div>
      </div>
    </header>
    <div class="tagline-band">Nourishing Food From the heart. Coffee at its best</div>
    <div class="gallery">
      <div class="photo-frame"><div class="photo photo--latte" role="img" aria-label="Photo of a latte with leaf art in a brown cup"></div></div>
      <div class="photo-frame"><div class="photo photo--cupcakes" role="img" aria-label="Photo of chocolate cupcakes topped with pink fairy floss"></div></div>
      <div class="photo-frame"><div class="photo photo--avocado-toast" role="img" aria-label="Photo of poached eggs on smashed avocado toast"></div></div>
      <div class="photo-frame"><div class="photo photo--tomato-toast" role="img" aria-label="Photo of poached eggs with grilled tomato on sourdough"></div></div>
    </div>
    <div class="address-band">384 Pelling Street, Marlow Heights QLD 4178, Australia</div>
  </section>

  <section class="card card--back">
    <h2 class="headline">OPEN FOR AFTER-SCHOOL MUNCHIES</h2>
    <p class="menu">Milkshakes, Frappes, All-natural Smoothies<br>Home-made burges, salads and Gourmet Sandwiches</p>
    <p class="social">Find us on Friendbook and Pictora</p>
  </section>
</body>
</html>
```